Design a modern, classy & professional business card for an online real estate agency, specializing in medium-luxury properties in Thailand and later in Singapore and UK.

Possible design ideas so far: (not essential)

- curved corner(s) to the card, white on front & turquoise on back or visa versa.

- front of card - clear and simple, company name in metallic grey/monochrome, logo graphic & company name on front in spot UV or embossed/debossed effect.

- back of card - large, close-cropped, 'ghost' patterns of the C-shaped curves of logo, or company name repeated on back of card in spot UV.

Target Market(s)

- young to middle-aged professionals mainly (but ideally should design should suit all)

- UK, US,EU,AUS & ASIAN mainly (but ideally should design should suit all countries)

Industry/Entity Type

Real Estate

Requirements
Must have
• THEME:
- Luxurious & Modern
- Clean & striking
- Unique & creative

INFO:
- Logo & company name on front
- Contact details on back:

Tobias Hennlund
Managing Director

www.velmontestates.asia
www.velmontestates.co.uk

Tel: 083-274-6159
email: tobias@velmontestates.asia

(contact details can be displayed in any order as suites design.)

Nice to have
• - curved corner(s) to the card, white on front & turquoise on back or visa versa.

Should not have
• - No generic images of properties, palm trees/coconut trees etc.

- No other other bold colors, except for main turquoise, grey, metallic white & black theme.

- No obvious business card templates

```html
<!DOCTYPE html>
<html lang="en">
<head>
<meta charset="utf-8">
<title>Velmont Estates — Business Card</title>
<link rel="stylesheet" href="https://fonts.googleapis.com/css2?family=Arimo:wght@400&family=Tinos:wght@400&display=swap">
<style>
  :root {
    --stage-centre: #3c5d9e;
    --stage-mid: #1a2647;
    --stage-edge: #050608;
    --card-front: #c9cdca;
    --card-front-shade: #b4b9b6;
    --card-back: #d6d9d6;
    --card-back-shade: #c3c7c4;
    --turquoise: #17c7c4;
    --logo-grey: #6f7070;
    --name-grey: #666868;
    --title-brown: #3b1a1c;
    --text-dark: #111;
    --rule: #555;
  }
  * { box-sizing: border-box; margin: 0; padding: 0; }
  html, body { width: 1200px; height: 889px; overflow: hidden; }
  body {
    position: relative;
    background: radial-gradient(ellipse 620px 520px at 600px 430px,
      var(--stage-centre) 0%, var(--stage-mid) 55%, var(--stage-edge) 100%);
  }
  .card {
    position: absolute;
    width: 708px;
    height: 405px;
    border-radius: 130px 0 120px 0;
    overflow: hidden;
  }
  .card--front {
    left: 85px; top: 38px;
    background: linear-gradient(135deg, var(--card-front) 0%, var(--card-front-shade) 100%);
  }
  .card--back {
    left: 427px; top: 425px;
    background: linear-gradient(135deg, var(--card-back-shade) 0%, var(--card-back) 60%);
  }
  .brand { position: absolute; }
  .brand__mark { position: absolute; left: 0; top: 0; background: var(--turquoise); }
  .brand__name, .brand__sub {
    position: absolute;
    font-family: "Tinos", "Times New Roman", serif;
    font-weight: 400;
    color: var(--logo-grey);
    white-space: nowrap;
    line-height: 1;
  }
  .card--front .brand { left: 143px; top: 144px; }
  .card--front .brand__mark { width: 120px; height: 119px; }
  .card--front .brand__name { left: 134px; top: 18px; font-size: 86px; }
  .card--front .brand__sub { left: 142px; top: 94px; font-size: 27px; letter-spacing: 9px; }

  .card--back .brand { left: 341px; top: 33px; }
  .card--back .brand__mark { width: 90px; height: 90px; }
  .card--back .brand__name { left: 100px; top: 9px; font-size: 64px; }
  .card--back .brand__sub { left: 106px; top: 66px; font-size: 20px; letter-spacing: 7px; }

  .person { position: absolute; left: 0; right: 0; text-align: center; }
  .person__name {
    position: absolute; left: 363px; top: 182px; width: 0;
    font-family: "Arimo", Arial, sans-serif; font-size: 38px; color: var(--name-grey);
    white-space: nowrap; display: flex; justify-content: center;
  }
  .person__title {
    position: absolute; left: 353px; top: 232px; width: 0;
    font-family: "Tinos", "Times New Roman", serif; font-size: 25px; color: var(--title-brown);
    white-space: nowrap; display: flex; justify-content: center;
  }
  .contact {
    position: absolute; left: 38px; top: 311px; width: 602px; height: 65px;
    border-top: 1px solid var(--rule); border-bottom: 1px solid var(--rule);
    font-family: "Arimo", Arial, sans-serif; font-size: 17.5px; color: var(--text-dark);
    line-height: 22px;
  }
  .contact__list { position: absolute; top: 9px; list-style: none; white-space: nowrap; }
  .contact__list--direct { left: 2px; }
  .contact__list--web { left: 353px; }
  .contact__label { display: inline-block; width: 55px; }
</style>
</head>
<body>
  <section class="card card--front" aria-label="Card front">
    <div class="brand">
      <span class="brand__mark"></span>
      <span class="brand__name">Velmont</span>
      <span class="brand__sub">ESTATES</span>
    </div>
  </section>

  <section class="card card--back" aria-label="Card back">
    <div class="brand">
      <span class="brand__mark"></span>
      <span class="brand__name">Velmont</span>
      <span class="brand__sub">ESTATES</span>
    </div>
    <p class="person__name">Tobias Hennlund</p>
    <p class="person__title">Managing Director</p>
    <div class="contact">
      <ul class="contact__list contact__list--direct">
        <li><span class="contact__label">Tel</span>: 083-274-6159</li>
        <li>email : tobias@velmontestates.asia</li>
      </ul>
      <ul class="contact__list contact__list--web">
        <li>www.velmontestates.asia</li>
        <li>www.velmontestates.co.uk</li>
      </ul>
    </div>
  </section>
</body>
</html>
```